Harborline Renewal Business Card Design

Professional and clean design. The design colors should flow with the logo. Two-sided card with the website on the back which is:

www.HarborlineRenewal.example.

"Specializing in Water Damage Restoration"

On the front I need the name, email, phone, and logo.

Name: Darnell Quisby
Email: Darnell@HarborlineRenewal.example
Phone: 555-318-2046 for now

I only have the Preview and Thumbnail right now but should have the source files uploaded within a day or two.

Target Market(s)

Flood victims, home owners with water damage from busted pipes etc...

Industry/Entity Type

Business

Contact Information for Business Card

Name: Darnell Quisby

Font styles to use
Serif
Sans Serif

Requirements
Must have
• Business Card Details Info

```html
<!DOCTYPE html>
<html lang="en">
<head>
<meta charset="utf-8">
<title>Harborline Renewal – Business Card</title>
<link rel="stylesheet" href="https://fonts.googleapis.com/css2?family=Arimo:wght@400;700&family=Cinzel:wght@500&display=swap">
<style>
  :root {
    --page: #ece9e4;
    --card-grey: #a4a4a4;
    --white: #ffffff;
    --brand-blue: #2c9fd8;
    --blue-deep: #1c8cc9;
    --swoosh-grey: #b9b9b9;
    --shadow: rgba(0,0,0,.18);
  }
  * { box-sizing: border-box; margin: 0; padding: 0; }
  html, body { width: 1200px; height: 950px; overflow: hidden; }
  body {
    background: var(--page);
    font-family: "Arimo", Arial, sans-serif;
    position: relative;
  }
  .card {
    position: absolute;
    left: 220px;
    width: 760px;
    height: 434px;
    border-radius: 4px;
    box-shadow: 0 8px 22px var(--shadow);
    overflow: hidden;
  }
  .card-back { top: 26px; background: var(--card-grey); }
  .card-front { top: 490px; background: var(--white); }

  .back-mark {
    position: absolute;
    top: 120px; left: 0; right: 0;
    display: flex; align-items: center; justify-content: center; gap: 16px;
  }
  .mark-dot {
    width: 38px; height: 38px; border-radius: 50%;
    border: 4px solid var(--white);
    flex: none;
  }
  .brand-name {
    font-family: "Cinzel", Georgia, serif;
    font-weight: 500;
    letter-spacing: 2px;
    text-transform: uppercase;
    white-space: nowrap;
  }
  .back-name { color: var(--white); font-size: 36px; }
  .tagline {
    position: absolute; top: 252px; left: 0; right: 0;
    text-align: center; color: var(--white);
    font-size: 20px; letter-spacing: .3px;
  }
  .back-web {
    position: absolute; top: 290px; left: 0; right: 0;
    text-align: center; color: var(--white);
    font-size: 17px; letter-spacing: .3px;
  }

  .front-waves { position: absolute; inset: 0; }
  .front-mark {
    position: absolute; top: 58px; left: 0; right: 0;
    display: flex; align-items: center; justify-content: center; gap: 14px;
  }
  .front-mark .mark-dot {
    width: 34px; height: 34px; border: none; background: var(--brand-blue);
  }
  .front-name { color: var(--brand-blue); font-size: 38px; }
  .holder-name {
    position: absolute; left: 40px; top: 366px;
    color: var(--white); font-size: 28px; font-weight: 700;
    white-space: nowrap;
  }
  .contact-list {
    position: absolute; left: 376px; top: 262px; right: 20px;
    list-style: none; color: var(--white); font-size: 17px;
  }
  .contact-list li {
    display: flex; align-items: center; gap: 9px; margin-bottom: 10px;
    white-space: nowrap;
  }
  .contact-list svg { width: 17px; height: 17px; flex: none; }
</style>
</head>
<body>

<section class="card card-back" aria-label="Card back">
  <div class="back-mark">
    <span class="mark-dot"></span>
    <span class="brand-name back-name">Harborline Renewal</span>
  </div>
  <p class="tagline">Specializing in Water Damage Restoration</p>
  <p class="back-web">www.HarborlineRenewal.example</p>
</section>

<section class="card card-front" aria-label="Card front">
  <svg class="front-waves" viewBox="0 0 760 434" preserveAspectRatio="none" aria-hidden="true">
    <path d="M0,282 C180,262 330,300 470,214 C580,150 690,118 760,104 L760,434 L0,434Z" fill="var(--swoosh-grey)"/>
    <path d="M0,298 C190,280 340,318 480,236 C590,172 695,142 760,128 L760,434 L0,434Z" fill="var(--brand-blue)"/>
    <path d="M0,434 L0,360 C200,370 420,330 760,250 L760,434Z" fill="var(--blue-deep)" opacity=".35"/>
  </svg>

  <div class="front-mark">
    <span class="mark-dot"></span>
    <span class="brand-name front-name">Harborline Renewal</span>
  </div>

  <p class="holder-name">Darnell Quisby</p>

  <ul class="contact-list">
    <li>
      <svg viewBox="0 0 24 24" aria-hidden="true"><path fill="#fff" d="M6.6 10.8a15 15 0 0 0 6.6 6.6l2.2-2.2a1 1 0 0 1 1-.25 11.4 11.4 0 0 0 3.6.57 1 1 0 0 1 1 1V20a1 1 0 0 1-1 1A17 17 0 0 1 3 4a1 1 0 0 1 1-1h3.5a1 1 0 0 1 1 1c0 1.25.2 2.45.57 3.57a1 1 0 0 1-.25 1Z"/></svg>
      555-318-2046 for now
    </li>
    <li>
      <svg viewBox="0 0 24 24" aria-hidden="true"><path fill="#fff" d="M2 5h20v14H2Zm2 2v.5l8 5 8-5V7Z"/></svg>
      Darnell@HarborlineRenewal.example
    </li>
    <li>
      <svg viewBox="0 0 24 24" aria-hidden="true"><circle cx="12" cy="12" r="9" fill="none" stroke="#fff" stroke-width="2"/><path d="M3 12h18M12 3c3 3 3 15 0 18M12 3c-3 3-3 15 0 18" fill="none" stroke="#fff" stroke-width="1.6"/></svg>
      HarborlineRenewal.example
    </li>
  </ul>
</section>

</body>
</html>
```